Local Roofing/Construction company business needs new biz card design

We need a new business card design, current cards are from the start of this operation and generic at best. We are a local Construction Company (General Contractor) with a majority of our work originating from insurance claims-exterior finish work is the main focus (Roofs-Siding-Gutters etc). Heavily involved with homeowners and the low ball offers they receive from insurance company's after a insurable event takes place. I have attached some of our original logo file(s) below.

```html
<!DOCTYPE html>
<html lang="en">
<head>
<meta charset="utf-8">
<title>Stonegate Construction – Business Card</title>
<link href="https://fonts.googleapis.com/css2?family=Montserrat:wght@400;500;600;800&display=swap" rel="stylesheet">
<style>
  :root{
    --backdrop:#3b3430;
    --card-white:#ffffff;
    --card-black:#111111;
    --ink:#1d1d1d;
    --ink-soft:#3a3a3a;
    --green:#22d36f;
    --pattern-light:#6a6a6a;
    --pattern-dark:#161616;
  }
  *{box-sizing:border-box;margin:0;padding:0}
  html,body{width:1200px;height:786px;overflow:hidden;background:var(--backdrop)}
  body{font-family:"Montserrat",sans-serif;position:relative}

  .card{position:absolute;top:238px;width:540px;height:310px;overflow:hidden;box-shadow:0 14px 30px rgba(0,0,0,.45)}
  .card--front{left:40px;background:var(--card-white)}
  .card--back{left:620px;background:var(--card-black)}

  /* front */
  .brand{position:absolute;left:34px;top:46px;color:var(--ink);font-weight:800;text-transform:uppercase;line-height:1}
  .brand__name{font-size:34px;letter-spacing:.5px}
  .brand__trade{font-size:17px;letter-spacing:2.4px;margin-top:4px}

  .brand-mark{position:absolute;right:40px;top:92px;width:200px;text-align:center;color:var(--green);font-weight:800;font-size:36px;line-height:1.05;text-transform:uppercase}
  .brand-mark__square{display:block;width:56px;height:56px;background:var(--green);margin:0 auto 14px}

  .person{position:absolute;left:34px;top:150px}
  .person__marker{position:absolute;left:-34px;top:4px;width:7px;height:32px;background:var(--green)}
  .person__name{color:var(--green);font-weight:600;font-size:20px}
  .person__role{color:var(--ink-soft);font-size:12px;margin-top:2px}

  .address{position:absolute;left:34px;top:204px;font-size:12.5px;color:var(--ink-soft);line-height:1.35}

  .contacts{position:absolute;left:34px;top:246px;list-style:none;font-size:12.5px;color:var(--ink-soft);line-height:1.45}
  .contacts li{display:flex;align-items:center;gap:8px}
  .contacts svg{width:11px;height:11px;fill:var(--green);flex:none}

  .edge-stripe{position:absolute;left:0;right:0;bottom:0;height:7px;background:var(--green)}

  /* back */
  .back-pattern{position:absolute;inset:0 0 22px 0;background:linear-gradient(110deg,var(--pattern-light) 0%,#3c3c3c 45%,var(--pattern-dark) 80%)}
  .back-name{position:absolute;right:48px;top:120px;color:var(--green);font-weight:800;font-size:22px;text-transform:uppercase;letter-spacing:.5px}
  .back-line{position:absolute;left:0;right:0;bottom:18px;height:4px;background:var(--green)}
</style>
</head>
<body>

<section class="card card--front" aria-label="Card front">
  <div class="brand">
    <div class="brand__name">Stonegate</div>
    <div class="brand__trade">Construction</div>
  </div>

  <div class="brand-mark">
    <span class="brand-mark__square"></span>
    Stone<br>gate
  </div>

  <div class="person">
    <span class="person__marker"></span>
    <div class="person__name">Dana Whitfield</div>
    <div class="person__role">Owner</div>
  </div>

  <address class="address">48 Orchard Bend Rd<br>Fairhollow, MO 63012</address>

  <ul class="contacts">
    <li>
      <svg viewBox="0 0 24 24" aria-hidden="true"><path d="M6.6 10.8a15.1 15.1 0 0 0 6.6 6.6l2.2-2.2c.3-.3.7-.4 1-.2 1.1.4 2.3.6 3.6.6.6 0 1 .4 1 1V20c0 .6-.4 1-1 1A17 17 0 0 1 3 4c0-.6.4-1 1-1h3.5c.6 0 1 .4 1 1 0 1.3.2 2.5.6 3.6.1.3 0 .7-.2 1z"/></svg>
      555-204-7731
    </li>
    <li>
      <svg viewBox="0 0 24 24" aria-hidden="true"><path d="M2 5h20v14H2zm2 2v.5l8 5 8-5V7z"/></svg>
      info@stonegatebuild.com
    </li>
    <li>
      <svg viewBox="0 0 24 24" aria-hidden="true"><circle cx="12" cy="12" r="10"/></svg>
      www.stonegatebuild.com
    </li>
  </ul>

  <div class="edge-stripe"></div>
</section>

<section class="card card--back" aria-label="Card back">
  <div class="back-pattern" role="img" aria-label="Repeating brand monogram pattern in glossy greys on black"></div>
  <div class="back-name">Stonegate</div>
  <div class="back-line"></div>
</section>

</body>
</html>
```